Business card for a Exhibition booth fabrication company

Hi. My company would like to change our corporate name card. We are an events and Exhibition stand builder company. We would like our corporate name card to resonate what we do. I need someone to create something unique that relates to the industry that I am in. The graphic designer should be creative to incorporate the elements of my industry and try to blend in well in the design of the card. Our aim is to ensure that we are unique and our card can look different from our competitors.
Updates

Target Market(s)

Marketing and events manager from all companies

Contact Information for Business Card

The business card should have the following details:
Name
Job Title
Email
Website

Colors

Designer to choose colors to be used in the design.

Requirements
Must have
• The card must be look something that is relevant to the service that I am providing. My website is: www.velmora-buildworks.com
• You can see my website to get more information on what service that I am doing
Nice to have
• On the back of my card, I would like to have a globe image with the incorporation of my company logo. This is to indicate that my services can be done in any part of the world.

```html
<!DOCTYPE html>
<html lang="en">
<head>
<meta charset="utf-8">
<title>Velmora Buildworks – Business Card</title>
<link rel="stylesheet" href="https://fonts.googleapis.com/css2?family=Arimo:wght@400;700&family=Source+Sans+3:wght@400&display=swap">
<style>
  :root {
    --brand-red: #ed1c24;
    --brand-red-light: #f15a60;
    --brand-grey: #6d6e71;
    --text-grey: #58595b;
    --card-white: #ffffff;
    --stage-left: #dcdddf;
    --stage-right: #a5a6a9;
  }
  * { margin: 0; padding: 0; box-sizing: border-box; }
  html, body { width: 1200px; height: 1118px; overflow: hidden; }
  body {
    background: linear-gradient(90deg, var(--stage-left), var(--stage-right));
    position: relative;
    font-family: "Source Sans 3", "Myriad Pro", sans-serif;
  }
  .card {
    position: absolute;
    left: 223px;
    width: 754px;
    height: 433px;
    border-radius: 24px;
    overflow: hidden;
  }
  .card--front { top: 87px; background: var(--card-white); }
  .card--back { top: 577px; background: var(--brand-red); }
  .card__art { position: absolute; inset: 0; width: 754px; height: 433px; }

  .brand {
    position: absolute;
    left: 0; right: 0;
    display: flex;
    align-items: center;
    justify-content: center;
    gap: 16px;
    font-family: "Arimo", Arial, sans-serif;
    font-weight: 400;
    text-transform: uppercase;
  }
  .brand__dot { width: 34px; height: 34px; border-radius: 50%; flex: none; }
  .card--front .brand { top: 118px; color: var(--brand-grey); font-size: 30px; letter-spacing: 1.5px; }
  .card--front .brand__dot { background: var(--brand-red); }
  .card--back .brand { top: 228px; color: #d6d7d9; font-size: 34px; letter-spacing: 4px; }
  .card--back .brand__dot { background: #d6d7d9; }

  .holder {
    position: absolute;
    top: 202px; left: 0; right: 0;
    text-align: center;
    font-family: "Arimo", Arial, sans-serif;
    text-transform: uppercase;
  }
  .holder__name { color: var(--brand-red); font-weight: 700; font-size: 25px; }
  .holder__title { color: var(--text-grey); font-weight: 400; font-size: 20px; }

  .contacts {
    position: absolute;
    left: 0; right: 0;
    color: #fff;
    font-size: 18px;
    text-align: center;
  }
  .contacts__row {
    position: absolute;
    left: 0; right: 0;
    display: flex;
    justify-content: center;
    align-items: center;
    gap: 20px;
  }
  .contacts__item { display: inline-flex; align-items: center; gap: 9px; }
  .contacts__icon { width: 17px; height: 17px; flex: none; }
  .row-phone { top: 323px; }
  .row-online { top: 354px; }
  .row-address { top: 393px; }

  .back-site {
    position: absolute;
    top: 391px; left: 0; right: 0;
    text-align: center;
    color: #fff;
    font-size: 20px;
    letter-spacing: 3.5px;
  }
</style>
</head>
<body>

<section class="card card--front" aria-label="Business card front">
  <svg class="card__art" viewBox="0 0 754 433" aria-hidden="true">
    <path d="M0,262 C190,335 460,345 754,236 L754,433 L0,433 Z" fill="var(--brand-red)"/>
    <path d="M0,190 C160,262 400,300 608,290 C420,306 200,296 0,250 Z" fill="var(--brand-grey)"/>
  </svg>

  <div class="brand"><span class="brand__dot"></span><span class="brand__name">Velmora Buildworks</span></div>

  <p class="holder"><span class="holder__name">Daniel Harcourt,</span> <span class="holder__title">President</span></p>

  <div class="contacts">
    <div class="contacts__row row-phone">
      <span class="contacts__item">
        <svg class="contacts__icon" viewBox="0 0 24 24"><path fill="#fff" d="M6.6 10.8a15.1 15.1 0 0 0 6.6 6.6l2.2-2.2a1 1 0 0 1 1-.25 11.4 11.4 0 0 0 3.6.57 1 1 0 0 1 1 1V20a1 1 0 0 1-1 1A17 17 0 0 1 3 4a1 1 0 0 1 1-1h3.5a1 1 0 0 1 1 1c0 1.25.2 2.45.57 3.57a1 1 0 0 1-.25 1z"/></svg>
        012-555-0147
      </span>
    </div>
    <div class="contacts__row row-online">
      <span class="contacts__item">
        <svg class="contacts__icon" viewBox="0 0 24 24"><rect x="2" y="5" width="20" height="14" fill="#fff"/><path d="M2 5l10 8 10-8M2 19l7-7M22 19l-7-7" stroke="var(--brand-red)" stroke-width="1.5" fill="none"/></svg>
        info@velmorabuildworks.com
      </span>
      <span class="contacts__item">
        <svg class="contacts__icon" viewBox="0 0 24 24" fill="none" stroke="#fff" stroke-width="1.6"><circle cx="12" cy="12" r="10"/><ellipse cx="12" cy="12" rx="4.5" ry="10"/><path d="M2 12h20M4 7h16M4 17h16"/></svg>
        www.velmora-buildworks.com
      </span>
    </div>
    <div class="contacts__row row-address">Street Name, City Name, Zipcode - 01234</div>
  </div>
</section>

<section class="card card--back" aria-label="Business card back">
  <svg class="card__art" viewBox="0 0 754 433">
    <defs>
      <radialGradient id="map-tone" cx="50%" cy="45%" r="60%">
        <stop offset="0" stop-color="var(--brand-red-light)" stop-opacity="0.85"/>
        <stop offset="1" stop-color="var(--brand-red-light)" stop-opacity="0.35"/>
      </radialGradient>
    </defs>
    <rect x="0" y="58" width="754" height="288" fill="url(#map-tone)" role="img" aria-label="Faint world map spanning the card, showing global service reach"/>
  </svg>

  <div class="brand"><span class="brand__dot"></span><span class="brand__name">Velmora Buildworks</span></div>

  <p class="back-site">www.velmora-buildworks.com</p>
</section>

</body>
</html>
```